Business card design for holistic health care clinic

We need a double-sided business card design for our holistic health care clinic that integrates our logo design and also its color scheme. My business is called Valmira. It is an integrative medicine clinic. You have already done the logo for me. Please ensure an elegant and upscale design that is not cluttered, but still has all the necessary information (please see below for details).

Target Market(s)

Wellness, fitness, rehabilitation for educated, well-traveled open-minded clients who are focused on natural, organic, balanced and preventive healthcare and lifestyle.

Industry/Entity Type

Medical

Contact Information for Business Card

Modern, clean.

Number of Pages Required

1 page

Font styles to use
Serif
Sans Serif

Colors

Designer to choose colors to be used in the design.

Requirements
Must have
• Logo on one side, all other information on the other side.
• Other information should include:
• Tobias Wrenfeld - DOE, CPT, LMT
• 4100 East Marrow Drive
• Austin, TX 78119
• 512 555 0148
• 818 555 0192
• info@ValmiraHealth.example
• t.wrenfeld@ValmiraHealth.example
Nice to have
• Darker background on front - but not totally black - shaded/dark gray.

```html
<!DOCTYPE html>
<html lang="en">
<head>
<meta charset="utf-8">
<title>Valmira – Business Card</title>
<link rel="stylesheet" href="https://fonts.googleapis.com/css2?family=Nunito:wght@800&family=Roboto:ital,wght@0,400;0,500;1,400&family=Roboto+Condensed:wght@700&display=swap">
<style>
  :root {
    --backdrop: #ece8e2;
    --card-light: #f7f7f7;
    --card-dark: #252727;
    --brand-blue: #0a8fd0;
    --text-dark: #3a3a3a;
    --text-light: #ffffff;
    --rule-light: rgba(255,255,255,0.45);
  }
  * { box-sizing: border-box; margin: 0; padding: 0; }
  html, body {
    width: 1200px; height: 960px; overflow: hidden;
    background: var(--backdrop);
  }
  .canvas { position: relative; width: 1200px; height: 960px; }

  .card { position: absolute; width: 600px; height: 342px; }
  .card--info { left: 314px; top: 113px; background: var(--card-light); }
  .card--brand { left: 311px; top: 472px; background: var(--card-dark); }

  .wordmark {
    font-family: "Nunito", sans-serif; font-weight: 800;
    color: var(--brand-blue); letter-spacing: 1px; line-height: 1;
    white-space: nowrap;
  }
  .tagline-sub {
    font-family: "Nunito", sans-serif; font-weight: 800;
    color: var(--brand-blue); line-height: 1; white-space: nowrap;
  }

  /* info side */
  .card--info .brand-block {
    position: absolute; right: 46px; top: 72px; text-align: center;
  }
  .card--info .wordmark { font-size: 54px; }
  .card--info .tagline-sub { font-size: 15px; margin-top: 6px; }

  .contact {
    position: absolute; left: 45px; top: 207px;
    font-family: "Roboto", sans-serif; font-size: 14.5px;
    color: var(--text-dark); line-height: 20px;
  }
  .contact .label { color: var(--brand-blue); font-weight: 500; }
  .contact .address { margin-top: 3px; }

  .person {
    position: absolute; right: 43px; top: 204px; text-align: right;
  }
  .person .name {
    font-family: "Roboto Condensed", sans-serif; font-weight: 700;
    font-size: 20px; color: var(--brand-blue); line-height: 24px;
  }
  .person .credentials {
    font-family: "Roboto Condensed", sans-serif; font-weight: 700;
    font-size: 11.5px; color: var(--brand-blue); line-height: 15px;
  }
  .person .email {
    font-family: "Roboto", sans-serif; font-size: 14.5px;
    color: var(--text-dark); margin-top: 5px;
  }

  .web-row {
    position: absolute; left: 45px; right: 44px; top: 292px;
    display: flex; align-items: center; gap: 4px;
  }
  .web-row .url {
    font-family: "Roboto", sans-serif; font-size: 14px;
    letter-spacing: 2.2px; color: var(--text-dark); white-space: nowrap;
  }
  .web-row .accent-bar { flex: 1; height: 8px; background: var(--brand-blue); }

  /* brand side */
  .card--brand .brand-block {
    position: absolute; left: 0; right: 0; top: 130px; text-align: center;
  }
  .card--brand .wordmark { font-size: 70px; }
  .card--brand .tagline-sub { font-size: 19px; margin-top: 8px; }

  .motto {
    position: absolute; left: 90px; right: 90px; top: 283px;
    display: flex; align-items: center; gap: 8px;
  }
  .motto .rule { flex: 1; height: 1px; }
  .motto .rule--left { background: linear-gradient(to right, transparent, var(--rule-light)); }
  .motto .rule--right { background: linear-gradient(to left, transparent, var(--rule-light)); }
  .motto .text {
    font-family: "Roboto", sans-serif; font-style: italic;
    font-size: 18px; color: var(--text-light); white-space: nowrap;
  }
</style>
</head>
<body>
<main class="canvas">
  <section class="card card--info" aria-label="Business card, contact side">
    <div class="brand-block">
      <div class="wordmark">VALMIRA</div>
      <div class="tagline-sub">Integrative Holistic Medicine</div>
    </div>
    <div class="contact">
      <div><span class="label">P:</span> 512 555 0148</div>
      <div><span class="label">C:</span> 818 555 0192</div>
      <div class="address">4100 East Marrow Drive, Austin, TX 78119</div>
    </div>
    <div class="person">
      <div class="name">TOBIAS WRENFELD</div>
      <div class="credentials">DOE, CPT, LMT</div>
      <div class="email">t.wrenfeld@ValmiraHealth.example</div>
    </div>
    <div class="web-row">
      <span class="url">www.ValmiraHealth.example</span>
      <span class="accent-bar"></span>
    </div>
  </section>

  <section class="card card--brand" aria-label="Business card, logo side">
    <div class="brand-block">
      <div class="wordmark">VALMIRA</div>
      <div class="tagline-sub">Integrative Holistic Medicine</div>
    </div>
    <div class="motto">
      <span class="rule rule--left"></span>
      <span class="text">helping the body help itself</span>
      <span class="rule rule--right"></span>
    </div>
  </section>
</main>
</body>
</html>
```